Real Estate Conference Exhibition Banner Design

We need a exhibition banner design for our company called Ledger Lantern Partners.
We are a consultancy business providing Trust Accounting, Training and Compliance services for the Real Estate Agencies around Australia. Our core focus is helping real estate agents with the Trust Accounts as an outsourced partner.

There are three banners and a case wrap all up.
The banners should use our logo colors being orange and grey.

Logo and banner templates supplied.
Upload file 5 is an example of the banner package we are purchasing.
Upload file 6,7,8 & 9 are some examples of banners we like.

our website is: ledgerlanternpartners.com.au

Target Market(s)

Real Estate Directors and Sales Agents

Industry/Entity Type

Business

Font styles to use
Sans Serif

Requirements
Must have
• Must make use of our company colours and include our logo.
Nice to have
• Would be happy to purchase stock photos

```html
<!DOCTYPE html>
<html lang="en">
<head>
<meta charset="utf-8">
<title>Ledger Lantern Partners – Exhibition Banner</title>
<link href="https://fonts.googleapis.com/css2?family=Lato:wght@300;400;700&display=swap" rel="stylesheet">
<style>
  :root {
    --page-bg: #eeeeee;
    --grey-band: #7a7a7a;
    --orange: #e8801f;
    --orange-deep: #d96f12;
    --orange-soft: #f0a04a;
    --white-band: #f4f4f4;
    --text-dark: #333333;
    --text-light: #ffffff;
    --bullet: #d9d9d9;
  }
  * { box-sizing: border-box; margin: 0; padding: 0; }
  html, body { width: 1200px; height: 943px; overflow: hidden; }
  body {
    background: var(--page-bg);
    font-family: "Lato", Arial, sans-serif;
    position: relative;
  }
  .banner {
    position: absolute;
    left: 40px; top: 110px;
    width: 1120px; height: 720px;
    background: var(--orange);
    overflow: hidden;
  }
  .top-band {
    position: absolute; left: 0; top: 0;
    width: 100%; height: 72px;
    background: var(--grey-band);
    display: flex; align-items: center; justify-content: flex-end;
    padding-right: 50px; gap: 18px;
  }
  .website {
    color: var(--text-light);
    font-size: 30px; font-weight: 400;
    letter-spacing: 0.2px;
  }
  .social-icons { display: flex; gap: 6px; }
  .social-icons span {
    width: 26px; height: 26px; border-radius: 50%;
    background: var(--white-band);
    opacity: 0.85;
  }
  .accent-stripe {
    position: absolute; left: 0; top: 72px;
    width: 100%; height: 16px;
    background: var(--orange);
  }
  .white-band {
    position: absolute; left: 0; top: 88px;
    width: 100%; height: 162px;
    background: linear-gradient(90deg, #e9e9e9, var(--white-band) 40%, #fafafa);
  }
  .brand-name {
    position: absolute; left: 130px; top: 40px;
    color: var(--orange);
    font-weight: 400;
    text-align: center;
    line-height: 1;
  }
  .brand-name .line-small {
    display: block;
    font-size: 20px; letter-spacing: 9px;
  }
  .brand-name .line-large {
    display: block;
    font-size: 58px; letter-spacing: 14px;
    margin-top: 6px;
  }
  .tagline {
    position: absolute; left: 620px; top: 44px;
    color: var(--text-dark);
    font-size: 31px; font-weight: 300;
    line-height: 48px;
  }
  .photo-area {
    position: absolute; left: 520px; top: 250px;
    width: 600px; height: 470px;
    background: linear-gradient(135deg, var(--orange-deep) 0%, var(--orange-soft) 45%, #e6dccf 80%, #cfcfcf 100%);
  }
  .feature-list {
    position: absolute; left: 130px; top: 340px;
    list-style: none;
    color: var(--text-light);
    font-size: 29px; font-weight: 400;
    line-height: 44px;
    width: 420px;
  }
  .feature-list li {
    position: relative;
    padding-left: 36px;
    margin-bottom: 22px;
    text-shadow: 1px 2px 3px rgba(0,0,0,0.25);
  }
  .feature-list li::before {
    content: "";
    position: absolute; left: 0; top: 16px;
    width: 12px; height: 14px;
    background: var(--bullet);
  }
</style>
</head>
<body>
  <section class="banner">
    <header class="top-band">
      <span class="website">ledgerlanternpartners.com.au</span>
      <div class="social-icons" aria-label="Social media links">
        <span></span><span></span><span></span><span></span>
      </div>
    </header>
    <div class="accent-stripe"></div>
    <div class="white-band">
      <div class="brand-name">
        <span class="line-small">LEDGER LANTERN</span>
        <span class="line-large">PARTNERS</span>
      </div>
      <p class="tagline">SERVING REAL ESTATE AGENCIES<br>ACROSS AUSTRALIA</p>
    </div>
    <div class="photo-area" role="img" aria-label="Photo of a stressed office worker at a desk with a laptop, over a soft orange house shape"></div>
    <ul class="feature-list">
      <li>Where there help When you need It most</li>
      <li>Cpt Points Training</li>
      <li>Helping Your Office Stay Complaint</li>
    </ul>
  </section>
</body>
</html>
```